larkforge website

commerce website to sell cookeries, brackets, mailboxes and to show off homes built. Modern Steel in design see marlo cycles web page to be like: https://www.marlocycles-demo.com/en/ sorry its bright nest hosting word press divi

must be able to add products to page

Target Market(s)

mainly western states of U.S.

Industry/Entity Type

Building Product

Coding

Coded - Design and coding required

Number of Pages Required

3 page

Font styles to use
Sans Serif

Colors

Designer to choose colors to be used in the design.

Requirements
Must have
• customers to be able to order products from page
• bright nest hosting word press divi

```html
<!DOCTYPE html>
<html lang="en">
<head>
<meta charset="utf-8">
<title>Larkforge</title>
<link href="https://fonts.googleapis.com/css2?family=Open+Sans:wght@300;400;600;700;800&display=swap" rel="stylesheet">
<style>
:root{
  --steel:#55618f;
  --steel-dark:#46527f;
  --mist:#e7e9ef;
  --mist-deep:#d9dce6;
  --ink:#2e2f36;
  --muted:#6b6e7a;
  --white:#ffffff;
}
*{box-sizing:border-box;margin:0;padding:0}
html,body{width:1200px;height:4200px;overflow:hidden}
body{font-family:"Open Sans",Arial,sans-serif;color:var(--ink);background:var(--white);position:relative}
.abs{position:absolute}
.btn{position:absolute;display:flex;align-items:center;justify-content:center;font-size:11px;font-weight:700;letter-spacing:.5px;text-transform:uppercase;border-radius:3px}
.btn-light{background:var(--white);color:var(--ink)}
.btn-steel{background:var(--steel);color:var(--white)}

/* header */
.brand{left:160px;top:22px;display:flex;align-items:center;gap:10px;color:var(--white);font-weight:800;font-size:22px;letter-spacing:1px}
.brand-dot{width:26px;height:26px;border-radius:50%;background:var(--white)}
.nav{left:412px;top:40px;display:flex;gap:26px;color:var(--white);font-size:12px;font-weight:600}
.login{left:924px;top:28px;width:86px;height:30px;border-radius:16px}

/* hero */
.hero-title{left:160px;top:262px;color:var(--white);font-size:40px;line-height:48px;font-weight:300;width:420px;text-transform:uppercase}
.hero-title b{font-weight:800}
.hero-cta{left:160px;top:452px;width:136px;height:40px}
.scroll-pill{left:590px;top:624px;width:16px;height:28px;border-radius:8px;background:var(--steel)}

/* welcome */
.welcome{left:780px;top:1000px;width:300px}
.welcome small{font-size:14px;color:var(--muted)}
.welcome h2{font-size:34px;font-weight:800;color:var(--steel);letter-spacing:1px;margin:2px 0 12px}
.welcome p{font-size:12px;line-height:20px;color:var(--muted)}
.about-btn{left:780px;top:1206px;width:136px;height:40px}

/* section headings */
.heading{left:0;width:1200px;text-align:center;font-size:38px;font-weight:300;color:var(--ink)}
.heading b{font-weight:800}
.intro{left:380px;width:440px;text-align:center;font-size:12px;line-height:20px;color:var(--muted)}

/* product cards */
.card{position:absolute;top:1770px;width:280px;height:370px}
.card-body{position:absolute;left:0;right:0;top:90px;bottom:0;background:var(--steel);border-radius:4px}
.card-img{position:absolute;left:30px;right:30px;top:0;height:190px;border-radius:6px}
.card h3{position:absolute;top:208px;width:100%;text-align:center;color:var(--white);font-size:17px;font-weight:600;text-transform:uppercase}
.card p{position:absolute;top:242px;left:30px;right:30px;text-align:center;color:#dfe3f0;font-size:11px;line-height:18px}
.card .btn{left:80px;top:310px;width:120px;height:34px}

/* testimonials */
.testi-title{left:320px;top:2406px;color:var(--white);font-size:36px;font-weight:700;letter-spacing:1px}
.testi-text{left:260px;top:2466px;width:420px;text-align:center;color:#e4e7f2;font-size:12px;line-height:20px}
.testi-name{left:260px;top:2554px;width:420px;text-align:center;color:var(--white);font-size:15px;font-weight:600}
.testi-rule{left:442px;top:2582px;width:56px;height:2px;background:var(--white)}
.arrow-btn{left:164px;top:2488px;width:32px;height:32px;border-radius:50%;border:2px solid var(--white);display:flex;align-items:center;justify-content:center}

/* offers */
.offer-box{left:262px;top:2970px;width:168px;height:236px;background:rgba(85,97,143,.88);color:var(--white);padding:26px 16px;text-align:center}
.offer-box h4{font-size:18px;font-weight:600;margin-bottom:10px}
.offer-box p{font-size:11px;line-height:18px;color:#e4e7f2}
.offer-icons{display:flex;justify-content:center;gap:14px;margin-top:22px}
.offer-icons span{width:34px;height:34px;border:1.5px solid var(--white);display:flex;align-items:center;justify-content:center}

/* newsletter */
.news-band{left:0;top:3410px;width:1200px;height:230px;background:var(--steel)}
.news-title{left:652px;top:3450px;color:var(--white);font-size:38px;font-weight:300}
.news-title b{font-weight:700}
.news-form{left:652px;top:3536px;width:370px;height:44px;border:1px solid rgba(255,255,255,.7);display:flex;align-items:center;padding-left:14px;gap:10px;color:#e4e7f2;font-size:11px}
.news-form .sub{margin-left:auto;height:100%;width:104px;background:var(--white);color:var(--ink);font-weight:700;font-size:11px;display:flex;align-items:center;justify-content:center}

/* contact */
.contact-title{left:160px;top:3720px;font-size:24px;font-weight:700;color:var(--steel);text-transform:uppercase}
.field{position:absolute;left:160px;width:340px;border:1px solid #c9ccd6;font-size:11px;color:var(--muted);padding:10px 12px}
.submit{left:160px;top:4030px;width:136px;height:42px}
.info-icon{left:580px;width:40px;height:40px}
.info-text{left:660px;font-size:12px;line-height:19px;color:var(--muted)}

/* footer */
.footer{left:0;top:4140px;width:1200px;height:60px;background:var(--steel);color:var(--white);font-size:11px;display:flex;align-items:center;justify-content:center}
</style>
</head>
<body>

<!-- hero background and photo -->
<svg class="abs" style="left:0;top:0" width="1200" height="720" viewBox="0 0 1200 720">
  <defs>
    <linearGradient id="buildingTone" x1="0" y1="0" x2="1" y2="1">
      <stop offset="0" stop-color="#8aa0b4"/>
      <stop offset=".55" stop-color="#5b6670"/>
      <stop offset="1" stop-color="#2f3438"/>
    </linearGradient>
  </defs>
  <path d="M0 0H1200V560C1080 610 980 640 840 630C700 620 640 560 520 550C380 540 300 610 160 640C90 655 40 640 0 620Z" fill="var(--steel)"/>
  <path role="img" aria-label="Modern steel-framed home exterior with glass walls and trees" d="M640 0H1200V480C1120 540 1020 560 920 540C800 515 720 440 660 340C610 250 600 120 640 0Z" fill="url(#buildingTone)"/>
</svg>

<div class="abs brand"><span class="brand-dot"></span>LARKFORGE</div>
<nav class="abs nav"><span>HOME</span><span>PRODUCTS</span><span>HOMES BUILT</span><span>ABOUT</span></nav>
<div class="btn btn-light login">Login</div>

<h1 class="abs hero-title">Lorem Ipsum is <b>simply</b> dummy text of the printing</h1>
<div class="btn btn-light hero-cta">Contact Us</div>
<div class="abs scroll-pill"></div>

<!-- welcome section -->
<svg class="abs" style="left:0;top:700px" width="1200" height="900" viewBox="0 0 1200 900">
  <defs>
    <linearGradient id="patioTone" x1="0" y1="0" x2="0" y2="1">
      <stop offset="0" stop-color="#7a6a5c"/>
      <stop offset=".6" stop-color="#9a8a78"/>
      <stop offset="1" stop-color="#5e6b4f"/>
    </linearGradient>
  </defs>
  <path d="M0 320C180 200 420 170 640 200C860 230 1020 170 1200 120V760C1020 800 820 760 640 700C440 640 200 690 0 760Z" fill="var(--mist)"/>
  <circle cx="280" cy="70" r="40" fill="var(--mist)"/>
  <circle cx="280" cy="70" r="16" fill="var(--white)"/>
  <rect x="160" y="158" width="430" height="514" rx="38" transform="rotate(-4 375 415)" fill="var(--steel)"/>
  <rect role="img" aria-label="Backyard patio with stone fire pit and outdoor seating" x="190" y="238" width="370" height="270" rx="18" fill="url(#patioTone)"/>
  <rect x="840" y="780" width="210" height="64" rx="32" transform="rotate(-16 945 812)" fill="var(--mist-deep)"/>
</svg>

<div class="abs welcome">
  <small>Welcome To</small>
  <h2>LARKFORGE</h2>
  <p>Lorem Ipsum is simply dummy text of the printing and typesetting industry. Lorem Ipsum has been the industry's standard dummy text ever since the 1500s, when an unknown printer took.</p>
</div>
<div class="btn btn-steel about-btn">About Us</div>

<!-- products -->
<h2 class="abs heading" style="top:1640px"><b>OUR</b> PRODUCT</h2>
<p class="abs intro" style="top:1702px">Lorem Ipsum is simply dummy text of the printing and typesetting industry. Lorem Ipsum has been the industry's standard dummy text ever since the 1500s.</p>

<div class="card" style="left:160px">
  <div class="card-body"></div>
  <div class="card-img" role="img" aria-label="Black steel fire table" style="background:linear-gradient(180deg,#f4f4f6 0%,#3a3a3e 60%,#f4f4f6 100%)"></div>
  <h3>Steel Cookery</h3>
  <p>Lorem Ipsum is simply dummy text of the printing and typesetting industry.</p>
  <div class="btn btn-light">Learn More</div>
</div>
<div class="card" style="left:460px">
  <div class="card-body"></div>
  <div class="card-img" role="img" aria-label="Galvanized steel post brackets" style="background:linear-gradient(180deg,#f4f4f6 0%,#b8bcc4 55%,#f4f4f6 100%)"></div>
  <h3>Brackets</h3>
  <p>Lorem Ipsum is simply dummy text of the printing and typesetting industry.</p>
  <div class="btn btn-light">Learn More</div>
</div>
<div class="card" style="left:760px">
  <div class="card-body"></div>
  <div class="card-img" role="img" aria-label="Black steel mailbox with red flag" style="background:linear-gradient(180deg,#f4f4f6 0%,#2c2c30 55%,#f4f4f6 100%)"></div>
  <h3>Mail Boxes</h3>
  <p>Lorem Ipsum is simply dummy text of the printing and typesetting industry.</p>
  <div class="btn btn-light">Learn More</div>
</div>

<!-- testimonials -->
<svg class="abs" style="left:0;top:2200px" width="1200" height="520" viewBox="0 0 1200 520">
  <path d="M0 110C120 80 260 90 420 60C560 35 680 0 780 20C860 36 880 110 860 200C840 300 860 400 760 450C640 505 480 470 320 480C180 488 80 500 0 510Z" fill="var(--steel)"/>
  <circle cx="800" cy="280" r="98" fill="var(--white)"/>
  <circle role="img" aria-label="Customer portrait" cx="800" cy="280" r="82" fill="#6f7a94"/>
  <circle role="img" aria-label="Customer portrait" cx="868" cy="80" r="24" fill="#7a6f6a"/>
  <circle role="img" aria-label="Customer portrait" cx="980" cy="200" r="20" fill="#6d7686"/>
  <circle role="img" aria-label="Customer portrait" cx="1118" cy="132" r="22" fill="#8a7466"/>
  <circle role="img" aria-label="Customer portrait" cx="1116" cy="290" r="22" fill="#7c6a70"/>
  <circle role="img" aria-label="Customer portrait" cx="1002" cy="362" r="20" fill="#6a6a72"/>
</svg>
<div class="abs arrow-btn"><svg width="12" height="12" viewBox="0 0 12 12"><path d="M8 1L3 6L8 11" fill="none" stroke="#fff" stroke-width="2"/></svg></div>
<h2 class="abs testi-title">TESTIMONIALS</h2>
<p class="abs testi-text">Lorem Ipsum is simply dummy text of the printing and typesetting industry. Lorem Ipsum has been the industry's standard dummy text ever since the 1500s.</p>
<div class="abs testi-name">Lorem Ipsum</div>
<div class="abs testi-rule"></div>

<!-- offers -->
<h2 class="abs heading" style="top:2770px"><b>GET SPECIAL</b> OFFERS</h2>
<p class="abs intro" style="top:2834px">Lorem Ipsum is simply dummy text of the printing and typesetting industry. Lorem Ipsum has been the industry's standard dummy text ever since the 1500s.</p>

<div class="abs" role="img" aria-label="Modern home interior with glass and steel" style="left:160px;top:2900px;width:420px;height:380px;background:linear-gradient(135deg,#4b5560,#2b3036 60%,#56606a)"></div>
<div class="abs offer-box">
  <h4>LOREM IPSUM</h4>
  <p>Lorem Ipsum is simply dummy text of the printing and typesetting industry.</p>
  <div class="offer-icons">
    <span><svg width="16" height="16" viewBox="0 0 16 16"><path d="M1 2h3l2 8h8l1-6H5" fill="none" stroke="#fff" stroke-width="1.5"/><circle cx="7" cy="13" r="1.3" fill="#fff"/><circle cx="13" cy="13" r="1.3" fill="#fff"/></svg></span>
    <span><svg width="16" height="16" viewBox="0 0 16 16"><path d="M8 14L2 8a3.3 3.3 0 0 1 6-4a3.3 3.3 0 0 1 6 4Z" fill="none" stroke="#fff" stroke-width="1.5"/></svg></span>
  </div>
</div>
<div class="abs" role="img" aria-label="Evening patio with fire pit and lounge chairs" style="left:620px;top:2900px;width:420px;height:170px;background:linear-gradient(135deg,#6b6058,#3d3a38 60%,#8a7a68)"></div>
<div class="abs" role="img" aria-label="Outdoor courtyard with fire table" style="left:620px;top:3104px;width:420px;height:176px;background:linear-gradient(135deg,#7a6e62,#4a4642 55%,#9a8c7c)"></div>

<!-- newsletter -->
<div class="abs news-band"></div>
<div class="abs" role="img" aria-label="Smiling man working on a laptop" style="left:150px;top:3240px;width:320px;height:400px;border-radius:160px 160px 0 0;background:linear-gradient(180deg,#8a7e76,#3f4a66 60%,#e9eaee)"></div>
<h2 class="abs news-title">Join Our <b>Newsletter</b></h2>
<div class="abs news-form">
  <svg width="14" height="12" viewBox="0 0 14 12"><rect x="1" y="1" width="12" height="10" fill="none" stroke="#fff"/><path d="M1 1l6 5l6-5" fill="none" stroke="#fff"/></svg>
  Enter Your E-mail Address
  <span class="sub">SUBSCRIBE</span>
</div>

<!-- contact -->
<h2 class="abs contact-title">Contact Us</h2>
<div class="field" style="top:3780px;height:40px">Name</div>
<div class="field" style="top:3840px;height:40px">E-mail</div>
<div class="field" style="top:3900px;height:100px">Message</div>
<div class="btn btn-steel submit">Submit</div>

<svg class="abs info-icon" style="top:3830px" viewBox="0 0 40 40"><path d="M20 4a10 10 0 0 0-10 10c0 8 10 20 10 20s10-12 10-20A10 10 0 0 0 20 4Z" fill="var(--steel)"/><circle cx="20" cy="14" r="4" fill="#fff"/></svg>
<p class="abs info-text" style="top:3830px">123 - Some street in dummy text,<br>Reno Nevada, USA</p>
<svg class="abs info-icon" style="top:3920px" viewBox="0 0 40 40"><path d="M11 6l6 2l-2 7l-3 2c2 5 5 8 10 10l2-3l7-2l2 6c-2 4-5 5-9 4C15 29 9 22 7 13c-1-4 1-6 4-7Z" fill="var(--steel)"/></svg>
<p class="abs info-text" style="top:3920px">CALL US<br>+1 555 014 2290</p>
<svg class="abs info-icon" style="top:4010px" viewBox="0 0 40 40"><rect x="5" y="10" width="30" height="20" rx="2" fill="var(--steel)"/><path d="M5 11l15 11l15-11" fill="none" stroke="#fff" stroke-width="2"/></svg>
<p class="abs info-text" style="top:4010px">MAIL US<br>info@larkforge-demo.com</p>

<footer class="abs footer">© Larkforge - 2020 All Rights Reserved</footer>

</body>
</html>
```